Rapid Pulse Tiny Track Karts

We are looking for a full web site for our race car category that allows us to edit and update some of the content. We would like the site to feel modern and attractive with the following features: 1. Event calender (with the ability for us to update) 2. Social media/ clip wave links 3. photo gallery (with the ability for us to update) 4. Member area with log in access (controlled access) - this area to include access to category regulations for up to 5 types of cars separately 5. Championship ladder for up to 5 different groups 6. sponsor page and sponsors scrolling across bottom of all pages. Please find attached our logo to be used and for reference on color/ style 7. page to show merchandise but no need for a store.

Industry/Entity Type

Motor racing category

Coding

Coded - Design and coding required

Number of Pages Required

5+ page

Colors
0054AA
0677BA
7BADD7
CADEEF
E8F1F8
FFF300
FFF600
FEFA6F
FFFEC7
FFFEE8
EB3D1F
EC4F4E
F09395
F8D3D4
FCEDEE

Requirements
Must have
• Ability to update calender/photo gallery/championship ladder including points/ notice board - Members section

```html
<!DOCTYPE html>
<html lang="en">
<head>
<meta charset="utf-8">
<title>Rapid Pulse Tiny Track Karts</title>
<link href="https://fonts.googleapis.com/css2?family=Bungee&family=Montserrat:wght@400;500;600;700&display=swap" rel="stylesheet">
<style>
:root{
  --blue:#27309f;
  --red:#e3141b;
  --yellow:#ffd000;
  --ink:#111111;
  --dark:#1c1c1c;
  --grey:#e4e4e4;
  --white:#ffffff;
  --head:"Bungee", sans-serif;
  --body:"Montserrat", sans-serif;
}
*{box-sizing:border-box;margin:0;padding:0}
html,body{width:1200px;height:4114px;overflow:hidden}
body{position:relative;background:var(--white);font-family:var(--body);color:var(--ink)}
.abs{position:absolute}
.brand{position:absolute;background:#fff;border:4px solid var(--ink);border-radius:10px;display:flex;align-items:center;justify-content:center;gap:10px;font-family:var(--head);color:var(--ink);text-align:center;line-height:1.1}
.brand .dot{width:18px;height:18px;border-radius:50%;background:var(--red);flex:none}
.topbar{left:424px;top:0;width:776px;height:67px;background:var(--blue);clip-path:polygon(30px 0,100% 0,100% 100%,0 100%);display:flex;align-items:center;gap:28px;padding-left:48px;color:#fff;font-size:12px;font-weight:600}
.topbar .item{display:flex;align-items:center;gap:10px;line-height:1.3}
.ico{width:28px;height:28px;background:#fff;border-radius:5px;display:flex;align-items:center;justify-content:center;flex:none}
.nav{left:462px;top:88px;display:flex;align-items:center;gap:32px;font-family:var(--head);font-size:11px;letter-spacing:1px}
.pill{padding:5px 14px;border-radius:6px;font-size:11px}
.pill.yellow{background:var(--yellow)}
.pill.red{background:var(--red);color:#fff}
.rule{left:0;width:1200px;height:4px;background:var(--red)}
.hero{left:0;top:152px;width:1200px;height:613px;background:linear-gradient(90deg,#3fae2a 0%,#5aa62d 25%,#2a3f8f 55%,#1f3fae 75%,#3a3d52 100%)}
.hero-text{left:112px;top:330px;font-family:var(--head);color:#fff;font-size:34px;line-height:49px;letter-spacing:3px}
.hero-text .sm{font-size:30px}
.btn{display:inline-block;background:var(--red);color:#fff;font-family:var(--head);font-size:11px;line-height:16px;padding:3px 12px;border-radius:5px;letter-spacing:1px}
.chev{position:absolute;width:26px;height:26px}
.sec-title{left:0;width:1200px;text-align:center;font-family:var(--head);font-size:28px;letter-spacing:3px}
.sec-title span{color:var(--red)}
.event-card{left:112px;top:997px;width:459px;height:331px;background:linear-gradient(160deg,#8a2a8f 0%,#3f6b2b 45%,#2a3a1f 100%)}
.event-date{left:275px;top:1016px;color:#fff;font-weight:600;font-size:21px;display:flex;gap:12px;align-items:center}
.event-name{left:144px;top:1262px;color:#fff;font-weight:600;font-size:26px}
.cal{left:488px;top:920px;width:581px;height:459px;background:#fff;box-shadow:0 0 8px rgba(0,0,0,.25)}
.cal-inner{position:absolute;left:16px;top:12px;width:549px;height:430px;border:2px solid var(--ink)}
.cal-head{position:absolute;left:86px;top:22px;width:384px;height:44px;background:var(--blue);display:flex;align-items:center;justify-content:space-between;padding:0 6px}
.cal-head b{color:#fff;font-size:25px;font-weight:600}
.cal-btn{width:36px;height:32px;background:#fff;display:flex;align-items:center;justify-content:center}
.cal-line{position:absolute;left:0;top:78px;width:100%;height:2px;background:#555}
.cal-grid{position:absolute;left:74px;top:94px;display:grid;grid-template-columns:repeat(7,63px);row-gap:14px;text-align:center;font-weight:700;font-size:20px}
.cal-grid .d{width:28px;height:26px;margin:0 auto;border:2px solid var(--ink);font-size:17px;line-height:22px}
.cal-grid .d.on{background:var(--red);border-color:var(--red)}
.merch{left:0;top:1480px;width:1200px;height:621px;background:radial-gradient(circle at 50% 30%,#6a3a1c 0%,#3a2010 55%,#1a0d06 100%)}
.merch-card{top:1598px;width:312px;height:447px;background:#fff;padding:10px}
.merch-img{width:100%;height:216px;border:2px solid #bbb}
.merch-card h3{font-family:var(--head);font-size:15px;margin:22px 6px 4px;letter-spacing:1px;font-weight:400}
.merch-card p{font-size:14px;line-height:31px;margin:0 6px;text-align:justify}
.merch-card .btn{margin:6px 6px 0}
.ladder{left:195px;top:2269px;width:810px;height:419px;border:8px solid var(--red);border-radius:28px;overflow:hidden;background:#fff}
.lad-head{height:62px;background:var(--blue);display:flex;align-items:center;color:#fff;font-family:var(--head);font-size:14px}
.lad-row{height:65px;display:flex;align-items:center;font-size:18px;font-weight:500}
.lad-row:nth-child(odd){background:var(--grey)}
.pos{width:56px;height:46px;background:var(--yellow);font-family:var(--head);font-size:15px;display:flex;align-items:center;justify-content:center;margin-left:8px}
.c{text-align:center}
.gallery{left:0;top:2773px;width:1200px;height:560px;background:radial-gradient(circle at 50% 50%,#2a2a2a 0%,#141414 70%)}
.gal-img{top:2936px;height:280px;border:3px solid #ddd}
.sponsor{top:3520px;height:80px;width:236px;background:#fff;border-radius:6px;box-shadow:0 2px 6px rgba(0,0,0,.35);display:flex;align-items:center;justify-content:center;font-weight:700;font-size:24px;color:var(--red);letter-spacing:1px}
.footer{left:0;top:3693px;width:1200px;height:421px;background:var(--dark);color:#fff}
.fcol h4{font-family:var(--head);font-weight:400;font-size:14px;letter-spacing:1px;margin-bottom:12px}
.fcol a{display:block;color:#fff;text-decoration:none;font-size:13px;margin-bottom:15px;letter-spacing:1px}
.fc-item{display:flex;gap:12px;align-items:center;font-size:12px;font-weight:600;margin-bottom:30px;line-height:1.4}
</style>
</head>
<body>

<div class="brand" style="left:112px;top:3px;width:296px;height:117px;font-size:21px"><span class="dot"></span>Rapid Pulse<br>Tiny Track Karts</div>
<div class="abs topbar">
  <div class="item"><span class="ico"><svg width="16" height="18" viewBox="0 0 16 18"><path d="M8 1a6 6 0 0 0-6 6c0 4 6 10 6 10s6-6 6-10a6 6 0 0 0-6-6z" fill="#27309f"/><circle cx="8" cy="7" r="2.3" fill="#fff"/></svg></span>Lorem Ipsum<br>USA - 40218</div>
  <div class="item"><span class="ico"><svg width="16" height="16" viewBox="0 0 16 16"><path d="M3 1l3 3-2 2c1 2 3 4 5 5l2-2 3 3-2 3C7 15 1 9 1 3z" fill="#27309f"/></svg></span>+1 555 014 2290</div>
  <div class="item"><span class="ico"><svg width="18" height="14" viewBox="0 0 18 14"><rect x="1" y="1" width="16" height="12" fill="#27309f"/><path d="M1 1l8 7 8-7" stroke="#fff" stroke-width="1.5" fill="none"/></svg></span>info@rapidpulsekarts.example</div>
</div>
<nav class="abs nav"><span>Home</span><span>About Us</span><span>Merchandise</span><span>Sponsors</span><span>Gallery</span><span class="pill yellow">Contact Us</span><span class="pill red">Login</span></nav>

<div class="abs rule" style="top:146px"></div>
<div class="abs hero" role="img" aria-label="Close-up photo of a blue miniature race car on a green backdrop"></div>
<div class="abs hero-text"><div class="sm">Welcome to</div>Rapid Pulse Tiny<br>Track Karts<br><span class="btn" style="vertical-align:top;margin-top:2px">Contact Us</span></div>
<svg class="chev" style="left:36px;top:384px" viewBox="0 0 26 26"><path d="M18 2L7 13l11 11" stroke="#fff" stroke-width="5" fill="none"/></svg>
<svg class="chev" style="left:1108px;top:384px" viewBox="0 0 26 26"><path d="M8 2l11 11L8 24" stroke="#fff" stroke-width="5" fill="none"/></svg>
<div class="abs rule" style="top:766px"></div>

<div class="abs sec-title" style="top:858px">Event <span>Calendar</span></div>
<div class="abs cal">
  <div class="cal-inner">
    <div class="cal-head">
      <span class="cal-btn"><svg width="16" height="18"><path d="M14 1L2 9l12 8z" fill="#000"/></svg></span>
      <b>OCTOBER <svg width="18" height="12"><path d="M1 1h16L9 11z" fill="#fff"/></svg></b>
      <span class="cal-btn"><svg width="16" height="18"><path d="M2 1l12 8-12 8z" fill="#000"/></svg></span>
    </div>
    <div class="cal-line"></div>
    <div class="cal-grid">
      <div>M</div><div>T</div><div>W</div><div>T</div><div>F</div><div>S</div><div>S</div>
      <div></div><div></div><div></div><div></div><div></div><div></div><div class="d">1</div>
      <div class="d">2</div><div class="d">3</div><div class="d">4</div><div class="d">5</div><div class="d">6</div><div class="d">7</div><div class="d">8</div>
      <div class="d">9</div><div class="d">10</div><div class="d">11</div><div class="d">12</div><div class="d">13</div><div class="d">14</div><div class="d">15</div>
      <div class="d">16</div><div class="d">17</div><div class="d">18</div><div class="d">19</div><div class="d">20</div><div class="d">21</div><div class="d">22</div>
      <div class="d">23</div><div class="d">24</div><div class="d">25</div><div class="d">26</div><div class="d">27</div><div class="d on">28</div><div class="d">29</div>
      <div class="d">30</div><div class="d">31</div>
    </div>
  </div>
</div>
<div class="abs event-card" role="img" aria-label="Photo of a red miniature sports car on a green and purple backdrop"></div>
<div class="abs event-date"><svg width="40" height="34" viewBox="0 0 40 34"><rect x="4" y="6" width="32" height="26" fill="#fff"/><rect x="4" y="6" width="32" height="7" fill="#ddd"/><rect x="10" y="2" width="4" height="8" fill="#fff"/><rect x="26" y="2" width="4" height="8" fill="#fff"/></svg>OCTOBER&nbsp; 28 2023</div>
<div class="abs event-name">LOREM IPSUM</div>

<div class="abs rule" style="top:1476px"></div>
<div class="abs merch" role="img" aria-label="Dark warm-toned backdrop photo"></div>
<div class="abs sec-title" style="top:1530px;color:#fff">Merchandise</div>
<svg class="chev" style="left:44px;top:1804px" viewBox="0 0 26 26"><path d="M18 2L7 13l11 11" stroke="#fff" stroke-width="5" fill="none"/></svg>
<svg class="chev" style="left:1116px;top:1804px" viewBox="0 0 26 26"><path d="M8 2l11 11L8 24" stroke="#fff" stroke-width="5" fill="none"/></svg>
<div class="abs merch-card" style="left:112px">
  <div class="merch-img" role="img" aria-label="Photo of two black team T-shirts" style="background:linear-gradient(#f4f4f4,#dcdcdc)"></div>
  <h3>T-Shirts</h3>
  <p>Lorem ipsum dolor sit amet, consectetur adipiscing elit, sed do eiusmod tempor incididunt ut labore et dolore magna aliqua.</p>
  <span class="btn">View More</span>
</div>
<div class="abs merch-card" style="left:443px">
  <div class="merch-img" role="img" aria-label="Photo of a white team mug" style="background:linear-gradient(#e6e6e6,#bdbdbd)"></div>
  <h3>Lorem Ipsum</h3>
  <p>Lorem ipsum dolor sit amet, consectetur adipiscing elit, sed do eiusmod tempor incididunt ut labore et dolore magna aliqua.</p>
  <span class="btn">View More</span>
</div>
<div class="abs merch-card" style="left:773px">
  <div class="merch-img" role="img" aria-label="Photo of a yellow and black team backpack" style="background:linear-gradient(#f6f6f6,#e2d6b8)"></div>
  <h3>Bags</h3>
  <p>Lorem ipsum dolor sit amet, consectetur adipiscing elit, sed do eiusmod tempor incididunt ut labore et dolore magna aliqua.</p>
  <span class="btn">View More</span>
</div>
<div class="abs rule" style="top:2098px"></div>

<div class="abs" role="img" aria-label="Photo of a yellow miniature hatchback" style="left:0;top:2120px;width:280px;height:171px;background:linear-gradient(135deg,#f4f4f4,#f2d46a 55%,#eeeeee)"></div>
<div class="abs sec-title" style="top:2192px">Championship <span>Ladder</span></div>
<div class="abs ladder">
  <div class="lad-head">
    <div style="width:76px" class="c">Pos</div><div style="width:190px" class="c">Team</div><div style="width:170px"></div>
    <div style="width:60px" class="c">GP</div><div style="width:90px" class="c">W</div><div style="width:60px" class="c">D</div><div style="width:90px" class="c">L</div><div style="width:60px" class="c">PTS</div>
  </div>
  <div>
    <div class="lad-row"><div class="pos">01</div><div style="width:290px;padding-left:92px;letter-spacing:2px">LOREM IPSUM</div><div style="width:60px;margin-left:60px" class="c">20</div><div style="width:90px" class="c">16</div><div style="width:60px" class="c">2</div><div style="width:90px" class="c">2</div><div style="width:60px" class="c">34</div></div>
    <div class="lad-row"><div class="pos">02</div><div style="width:290px;padding-left:92px;letter-spacing:2px">LOREM IPSUM</div><div style="width:60px;margin-left:60px" class="c">20</div><div style="width:90px" class="c">16</div><div style="width:60px" class="c">2</div><div style="width:90px" class="c">2</div><div style="width:60px" class="c">34</div></div>
    <div class="lad-row"><div class="pos">03</div><div style="width:290px;padding-left:92px;letter-spacing:2px">LOREM IPSUM</div><div style="width:60px;margin-left:60px" class="c">20</div><div style="width:90px" class="c">16</div><div style="width:60px" class="c">2</div><div style="width:90px" class="c">2</div><div style="width:60px" class="c">34</div></div>
    <div class="lad-row"><div class="pos">04</div><div style="width:290px;padding-left:92px;letter-spacing:2px">LOREM IPSUM</div><div style="width:60px;margin-left:60px" class="c">20</div><div style="width:90px" class="c">16</div><div style="width:60px" class="c">2</div><div style="width:90px" class="c">2</div><div style="width:60px" class="c">34</div></div>
    <div class="lad-row"><div class="pos">05</div><div style="width:290px;padding-left:92px;letter-spacing:2px">LOREM IPSUM</div><div style="width:60px;margin-left:60px" class="c">20</div><div style="width:90px" class="c">16</div><div style="width:60px" class="c">2</div><div style="width:90px" class="c">2</div><div style="width:60px" class="c">34</div></div>
  </div>
</div>
<div class="abs" role="img" aria-label="Photo of a red miniature sedan" style="left:957px;top:2664px;width:243px;height:101px;background:linear-gradient(180deg,#ffffff 0%,#d4453f 50%,#e8e8e8 100%)"></div>

<div class="abs rule" style="top:2766px"></div>
<div class="abs gallery"></div>
<div class="abs sec-title" style="top:2822px;color:#fff">Our Gallery</div>
<svg class="chev" style="left:50px;top:3060px" viewBox="0 0 26 26"><path d="M18 2L7 13l11 11" stroke="#fff" stroke-width="5" fill="none"/></svg>
<svg class="chev" style="left:1122px;top:3060px" viewBox="0 0 26 26"><path d="M8 2l11 11L8 24" stroke="#fff" stroke-width="5" fill="none"/></svg>
<div class="abs gal-img" role="img" aria-label="Photo of an orange miniature hatchback" style="left:136px;width:283px;clip-path:polygon(0 12%,100% 0,100% 100%,0 88%);background:linear-gradient(160deg,#7fa4b8,#e28a3a 55%,#6c6c6c)"></div>
<div class="abs gal-img" role="img" aria-label="Photo of blue and green miniature race cars" style="left:429px;width:345px;background:linear-gradient(160deg,#9bb6e8,#3a4aa8 45%,#3ca83a 80%,#8fb0e0)"></div>
<div class="abs gal-img" role="img" aria-label="Photo of a yellow miniature muscle car" style="left:781px;width:283px;clip-path:polygon(0 0,100% 12%,100% 88%,0 100%);background:linear-gradient(160deg,#8c8c8c,#e5cf2a 55%,#6f6f6f)"></div>
<div class="abs rule" style="top:3334px"></div>

<div class="abs sec-title" style="top:3425px">Our Sponsors</div>
<svg class="chev" style="left:34px;top:3548px" viewBox="0 0 26 26"><path d="M18 2L7 13l11 11" stroke="#000" stroke-width="5" fill="none"/></svg>
<svg class="chev" style="left:1122px;top:3548px" viewBox="0 0 26 26"><path d="M8 2l11 11L8 24" stroke="#000" stroke-width="5" fill="none"/></svg>
<div class="abs sponsor" style="left:112px">KESTREL</div>
<div class="abs sponsor" style="left:357px">TORVANE</div>
<div class="abs sponsor" style="left:603px">HALDEN</div>
<div class="abs sponsor" style="left:850px">GRIT LANE</div>

<footer class="abs footer">
  <div class="brand" style="left:112px;top:83px;width:270px;height:100px;font-size:19px;border-color:#fff"><span class="dot"></span>Rapid Pulse<br>Tiny Track Karts</div>
  <p class="abs" style="left:112px;top:208px;width:284px;font-size:14px;line-height:30px;text-align:justify;letter-spacing:1px">Lorem ipsum dolor sit amet, consectetur adipiscing elit, sed do eiusmod tempor incididunt ut labore et dolore magna aliqua.</p>
  <div class="abs fcol" style="left:472px;top:96px"><h4>Quick Links</h4><a>Home</a><a>About Us</a><a>merchandise</a><a>sponsors</a><a>Gallery</a><a>Contact Us</a></div>
  <div class="abs fcol" style="left:651px;top:96px"><h4>Help Links</h4><a>Privacy Policy</a><a>Terms &amp; Conditions</a>
    <h4 style="margin-top:26px">Follow Us</h4>
    <a style="display:flex;align-items:center;gap:12px"><svg width="22" height="20"><rect width="22" height="20" rx="3" fill="#fff"/><path d="M8 5l8 5-8 5z" fill="#1c1c1c"/></svg>Clip Wave</a>
  </div>
  <div class="abs fcol" style="left:877px;top:96px"><h4>Contact Details</h4>
    <div class="fc-item"><span class="ico"><svg width="16" height="18" viewBox="0 0 16 18"><path d="M8 1a6 6 0 0 0-6 6c0 4 6 10 6 10s6-6 6-10a6 6 0 0 0-6-6z" fill="#1c1c1c"/><circle cx="8" cy="7" r="2.3" fill="#fff"/></svg></span>Lorem Ipsum<br>USA - 40218</div>
    <div class="fc-item"><span class="ico"><svg width="16" height="16" viewBox="0 0 16 16"><path d="M3 1l3 3-2 2c1 2 3 4 5 5l2-2 3 3-2 3C7 15 1 9 1 3z" fill="#1c1c1c"/></svg></span>+1 555 014 2290</div>
    <div class="fc-item"><span class="ico"><svg width="18" height="14" viewBox="0 0 18 14"><rect x="1" y="1" width="16" height="12" fill="#1c1c1c"/><path d="M1 1l8 7 8-7" stroke="#fff" stroke-width="1.5" fill="none"/></svg></span>info@rapidpulse<br>karts.example</div>
  </div>
  <div class="abs" style="left:112px;top:362px;width:976px;height:1px;background:#777"></div>
  <p class="abs" style="left:0;top:384px;width:1200px;text-align:center;font-size:13px">© 2023 COPYRIGHT Rapid Pulse Tiny Track Karts.ALL RIGHT RESERVED.</p>
</footer>
</body>
</html>
```